Oil Field Service company needs professional business cards

Looking to clean up our current company business cards and look a little more professional. Brenwick Casing Services is a US based company that services the oil field. We deal with engineers, managers and oil rigs....................................................................................................................................................................................................................................................................................................................................................................................................

Target Market(s)

Oil and Gas professionals

Industry/Entity Type

Oil And Gas

Contact Information for Business Card

See attached photo as example

Font styles to use
Sans Serif

Colors
ec1f27

Requirements
Must have
• Company Logo, Name, Title, Cell, Office, Fax, Email.
• See attached photo
Nice to have
• External CRT, Internal CRT, Casing Crews, Torque Turn, Laydown Machine
Should not have
• Do not introduce any new pictures and keep it professional looking

```html
<!DOCTYPE html>
<html lang="en">
<head>
<meta charset="utf-8">
<title>Brenwick Casing Services – Business Card</title>
<link href="https://fonts.googleapis.com/css2?family=Roboto:wght@400;500;700&display=swap" rel="stylesheet">
<style>
  :root {
    --brand-red: #ec1f27;
    --deep-red: #c8141b;
    --ink: #3a3a3a;
    --ink-soft: #4a4a4a;
    --card: #f3efe9;
    --backdrop: #d8d2c9;
  }
  * { margin: 0; padding: 0; box-sizing: border-box; }
  html, body {
    width: 1200px; height: 1047px; overflow: hidden;
    background: var(--backdrop);
    font-family: "Roboto", Arial, sans-serif;
  }
  .business-card {
    position: absolute; left: 100px; top: 253px;
    width: 1000px; height: 541px;
    background: var(--card);
    border-radius: 18px;
    overflow: hidden;
    box-shadow: 0 10px 30px rgba(0,0,0,0.12);
  }
  .company-mark {
    position: absolute; left: 74px; top: 108px; width: 355px;
    display: flex; align-items: center; gap: 14px;
    color: var(--ink); font-weight: 700;
  }
  .company-mark__square { width: 22px; height: 22px; background: var(--brand-red); flex: none; }
  .company-mark__name { font-size: 33px; line-height: 1.1; letter-spacing: 0.5px; }
  .service-list {
    position: absolute; left: 74px; top: 290px; width: 355px;
    text-align: center; color: var(--ink-soft);
    font-size: 21px; font-weight: 500; line-height: 32px; letter-spacing: 0.3px;
  }
  .person {
    position: absolute; right: 76px; top: 118px; text-align: right;
  }
  .person__name { color: var(--deep-red); font-size: 39px; font-weight: 700; line-height: 1.1; }
  .person__title { color: var(--ink); font-size: 22px; font-weight: 500; margin-top: 6px; }
  .side-tab {
    position: absolute; right: 0; top: 131px; width: 46px; height: 63px;
    background: var(--deep-red); border-radius: 8px 0 0 8px;
  }
  .contact-list {
    position: absolute; right: 66px; top: 248px; list-style: none;
  }
  .contact-list li {
    display: flex; justify-content: flex-end; align-items: center;
    height: 32.5px; color: var(--ink);
    font-size: 22px; font-weight: 500; letter-spacing: 0.5px;
  }
  .contact-list .icon { width: 24px; height: 24px; margin-left: 24px; flex: none; }
  .contact-list .icon--none { visibility: hidden; }
  .bottom-wave { position: absolute; left: 0; bottom: 0; width: 1000px; height: 100px; }
</style>
</head>
<body>
  <div class="business-card">
    <div class="company-mark">
      <span class="company-mark__square"></span>
      <span class="company-mark__name">Brenwick Casing Services</span>
    </div>

    <div class="service-list">
      <p>Laydown Machine | Casing Crew</p>
      <p>Mud Tools | Torque Turn</p>
    </div>

    <div class="person">
      <p class="person__name">Cody Harlan</p>
      <p class="person__title">Area Manager</p>
    </div>
    <div class="side-tab"></div>

    <ul class="contact-list">
      <li>(555) 210 4870
        <svg class="icon" viewBox="0 0 24 24" fill="none" stroke="var(--brand-red)" stroke-width="2"><rect x="7" y="2" width="10" height="20" rx="2"/><line x1="11" y1="18" x2="13" y2="18"/></svg>
      </li>
      <li>(555) 318 6024
        <svg class="icon" viewBox="0 0 24 24" fill="var(--brand-red)"><path d="M6.6 10.8a15 15 0 0 0 6.6 6.6l2.2-2.2a1 1 0 0 1 1-.25 11.4 11.4 0 0 0 3.6.6 1 1 0 0 1 1 1V20a1 1 0 0 1-1 1A17 17 0 0 1 3 4a1 1 0 0 1 1-1h3.5a1 1 0 0 1 1 1c0 1.25.2 2.45.6 3.6a1 1 0 0 1-.25 1z"/></svg>
      </li>
      <li>(555) 210 4871
        <svg class="icon" viewBox="0 0 24 24" fill="var(--brand-red)"><rect x="7" y="2" width="10" height="6"/><rect x="3" y="9" width="18" height="10" rx="2"/><rect x="6" y="15" width="12" height="7" fill="#fff"/><rect x="7.5" y="17" width="9" height="1.5"/></svg>
      </li>
      <li>cody@brenwickcasing.com
        <svg class="icon" viewBox="0 0 24 24" fill="none" stroke="var(--brand-red)" stroke-width="1.8"><rect x="3" y="5" width="18" height="14"/><polyline points="3,5 12,13 21,5"/></svg>
      </li>
      <li>Alder Springs, OK 73990
        <svg class="icon icon--none" viewBox="0 0 24 24"></svg>
      </li>
    </ul>

    <svg class="bottom-wave" viewBox="0 0 1000 100" preserveAspectRatio="none">
      <defs>
        <linearGradient id="waveRed" x1="0" y1="0" x2="1" y2="0">
          <stop offset="0" stop-color="#c8141b"/>
          <stop offset="0.5" stop-color="#e0232a"/>
          <stop offset="1" stop-color="#b81118"/>
        </linearGradient>
      </defs>
      <path d="M0 62 Q500 -55 1000 55 L1000 100 L0 100 Z" fill="url(#waveRed)"/>
    </svg>
  </div>
</body>
</html>
```